New web page, 2 companies on the one page

A new web page for an engineering consultancy and maintenance management company

Corlett & Associates is the parent company covering the design and consultancy
Valtrix Engineering is the Maintenance and Reliability company

Target Market(s)

Food & Beverage, ingredients Manufacturing
engineering managers

Coding

Coded - Design and coding required

Number of Pages Required

1 page

Font styles to use
Other font styles liked:
• Roboto

Colors
1861ab
85acd3
d0dfed
cee9f5

```html
<!DOCTYPE html>
<html lang="en">
<head>
<meta charset="utf-8">
<title>Corlett &amp; Associates</title>
<link href="https://fonts.googleapis.com/css2?family=Montserrat:wght@600;700&family=Roboto:ital,wght@0,400;0,500;0,700;1,400&display=swap" rel="stylesheet">
<style>
:root{
  --blue:#1861ab;
  --mid:#85acd3;
  --pale:#d0dfed;
  --sky:#cee9f5;
  --ink:#1a1a1a;
  --grey:#777;
  --dark:#333333;
  --white:#fff;
}
*{margin:0;padding:0;box-sizing:border-box}
html,body{width:1200px;height:3337px;overflow:hidden}
body{position:relative;font-family:Roboto,sans-serif;color:var(--ink);background:var(--white)}
.abs{position:absolute}
.heading{font-family:Montserrat,sans-serif;font-weight:700;letter-spacing:1px}
.btn{position:absolute;display:flex;align-items:center;justify-content:center;gap:12px;background:var(--blue);color:var(--white);font-weight:700;font-size:14px;text-transform:uppercase}
.btn svg{width:14px;height:14px}

/* header */
.brand{left:112px;top:34px;display:flex;align-items:center;gap:10px;font-weight:700;font-size:24px;color:var(--dark)}
.brand .mark{width:36px;height:36px;background:var(--blue);border-radius:4px}
.call{left:880px;top:15px;display:flex;gap:16px;align-items:center}
.call .ring{width:40px;height:40px;border:2px solid var(--pale);border-radius:50%;display:flex;align-items:center;justify-content:center}
.call small{display:block;font-size:11px;font-weight:700}
.call strong{display:block;font-size:23px;color:var(--blue);font-weight:700;line-height:1.1}
.nav{right:112px;top:80px;display:flex;gap:22px;font-size:14px;font-weight:500;text-transform:uppercase}
.nav .on{color:var(--blue)}

/* hero */
.hero{left:0;top:117px;width:1200px;height:608px}
.hero-title{top:300px;width:1200px;text-align:center;color:var(--white);font-size:48px}
.hero-sub{top:372px;left:290px;width:620px;text-align:center;color:var(--white);font-size:14px;line-height:27px}

/* about */
.about-visual{left:124px;top:865px;width:420px;height:438px;border-radius:30px;background:linear-gradient(135deg,#6b8fb3,#3d4d5c 60%,#c9a23a)}
.about-title{left:678px;top:890px;font-size:34px}
.about-text{left:678px;top:952px;width:420px;font-size:14px;line-height:30px;color:var(--grey)}
.rule{left:0;top:1406px;width:1200px;height:1px;background:#eee}

/* services */
.services-bg{left:0;top:1960px;width:1200px;height:428px;background:linear-gradient(#fff,#eef4fa)}
.section-title{width:1200px;text-align:center;font-size:36px}
.service{position:absolute;width:232px;text-align:center}
.service .icon{width:116px;height:116px;margin:0 auto;border-radius:50%;background:var(--white);box-shadow:0 4px 10px rgba(0,0,0,.12);display:flex;align-items:center;justify-content:center}
.service .icon span{width:92px;height:92px;border-radius:50%;display:flex;align-items:center;justify-content:center;background:var(--mid)}
.service .icon.soft span{background:var(--pale)}
.service h3{margin-top:36px;font-size:14px;font-weight:700;text-transform:uppercase}
.service p{margin-top:10px;font-size:13px;line-height:23px;color:var(--grey)}

/* testimonials */
.reviews{left:0;top:2388px;width:1200px;height:500px;background:linear-gradient(160deg,#d6ecf6,#b9d6e6 55%,#cfe6f1)}
.card{position:absolute;top:2574px;width:317px;height:211px;border-radius:14px 14px 0 0;background:var(--white);padding:26px 30px}
.card.featured{background:var(--mid);color:var(--white)}
.card .quote{font-family:Montserrat,sans-serif;font-size:44px;line-height:30px;color:var(--blue);font-weight:700;height:30px}
.card.featured .quote{color:var(--white)}
.card p{margin-top:8px;font-size:14px;font-style:italic;line-height:26px;color:var(--grey)}
.card.featured p{color:var(--white)}
.person{display:flex;align-items:center;gap:18px;margin-top:12px}
.avatar{width:48px;height:48px;border-radius:50%;background:#b8c3cc}
.person strong{display:block;font-size:14px;color:var(--blue);text-transform:uppercase}
.person span{font-size:14px;color:var(--blue)}
.card.featured .person strong,.card.featured .person span{color:var(--white)}

/* footer */
.footer{left:0;top:2888px;width:1200px;height:449px;background:var(--dark);color:var(--white)}
.foot-h{font-size:15px;font-weight:700;text-transform:uppercase}
.field{position:absolute;background:var(--white);border:1px solid #ccc;font-size:14px;color:#777;padding:12px 8px}
.info-row{position:absolute;left:628px;display:flex;gap:18px;font-size:14px;line-height:26px}
.info-row .dot{width:28px;height:28px;border-radius:50%;background:var(--white);display:flex;align-items:center;justify-content:center;flex:none}
.links{left:953px;top:2993px;list-style:none;font-size:14px;line-height:34.5px}
.links li::before{content:"»";margin-right:14px}
.social{position:absolute;width:28px;height:28px;border-radius:50%}
.foot-rule{left:112px;top:3260px;width:976px;height:1px;background:#444}
</style>
</head>
<body>

<!-- header -->
<div class="abs brand"><span class="mark"></span>CORLETT</div>
<div class="abs call">
  <div class="ring"><svg width="18" height="18" viewBox="0 0 24 24"><path d="M6.6 10.8a15 15 0 006.6 6.6l2.2-2.2a1 1 0 011-.25 11.4 11.4 0 003.6.57 1 1 0 011 1V20a1 1 0 01-1 1A17 17 0 013 4a1 1 0 011-1h3.5a1 1 0 011 1c0 1.25.2 2.45.57 3.6a1 1 0 01-.25 1z" fill="#1861ab"/></svg></div>
  <div><small>CALL US TODAY</small><strong>1 800 555 0142</strong></div>
</div>
<nav class="abs nav"><span class="on">Home</span><span>About Us</span><span>Our Services</span><span>Testimonials</span><span>Latest Blog</span><span>Contact Us</span></nav>

<!-- hero -->
<svg class="abs hero" viewBox="0 117 1200 608" role="img" aria-label="Aerial photograph of a harbour city skyline">
  <defs><linearGradient id="city" x1="0" y1="0" x2="0" y2="1">
    <stop offset="0" stop-color="#b9c0c6"/><stop offset=".45" stop-color="#5f6e6a"/><stop offset="1" stop-color="#2f6c72"/></linearGradient></defs>
  <polygon points="0,117 1200,117 1200,590 600,666 0,590" fill="url(#city)"/>
  <polygon points="0,590 600,666 600,725 0,640" fill="#85acd3"/>
  <polygon points="600,666 1200,590 1200,632 600,725" fill="#cee9f5"/>
</svg>
<div class="abs heading hero-title">CORLETT ASSOCIATES</div>
<p class="abs hero-sub">Corlett &amp; Associates is specialised manufacturing engineering support organisation that can provide fast, nimble, and flexible services.</p>
<div class="btn" style="left:518px;top:442px;width:165px;height:51px">Get Started <svg viewBox="0 0 16 16"><circle cx="8" cy="8" r="8" fill="#fff"/><path d="M6 4.5L9.5 8 6 11.5" stroke="#1861ab" stroke-width="2" fill="none"/></svg></div>

<!-- about -->
<div class="abs about-visual" role="img" aria-label="Technician testing an electrical control panel"></div>
<h2 class="abs heading about-title">ABOUT US</h2>
<p class="abs about-text">Corlett &amp; Associates is specialised manufacturing engineering support organisation that can provide fast, nimble, and flexible services. We have a proven track record in delivering tangible outcomes in process design and fit-out, project management, manufacturing process and maintenance design and execution. Our specialist focus in food manufacturing across a range of sectors allows our team to deliver real benefits to performance and recognition of the clients investment</p>
<div class="btn" style="left:678px;top:1217px;width:166px;height:52px">Learn More <svg viewBox="0 0 16 16"><circle cx="8" cy="8" r="8" fill="#fff"/><path d="M6 4.5L9.5 8 6 11.5" stroke="#1861ab" stroke-width="2" fill="none"/></svg></div>
<div class="abs rule"></div>

<!-- services -->
<div class="abs services-bg"></div>
<h2 class="abs heading section-title" style="top:1474px">OUR SERVICES</h2>

<div class="service" style="left:116px;top:1582px"><div class="icon"><span><svg width="40" height="40" viewBox="0 0 40 40"><circle cx="20" cy="20" r="10" stroke="#fff" stroke-width="2.5" fill="none"/><circle cx="20" cy="20" r="3" fill="#fff"/></svg></span></div><h3>Process &amp; Facilities Design</h3><p>Lorem ipsum dolor sit amet, consectetur adipiscing elit, sed do eiusmod tempor incididunt</p></div>
<div class="service" style="left:367px;top:1582px"><div class="icon soft"><span><svg width="40" height="40" viewBox="0 0 40 40"><circle cx="20" cy="20" r="10" stroke="#fff" stroke-width="2.5" fill="none"/><circle cx="20" cy="20" r="3" fill="#fff"/></svg></span></div><h3>Project Management</h3><p>Lorem ipsum dolor sit amet, consectetur adipiscing elit, sed do eiusmod tempor incididunt</p></div>
<div class="service" style="left:619px;top:1582px"><div class="icon"><span><svg width="40" height="40" viewBox="0 0 40 40"><circle cx="20" cy="20" r="10" stroke="#fff" stroke-width="2.5" fill="none"/><circle cx="20" cy="20" r="3" fill="#fff"/></svg></span></div><h3>Major Equipment</h3><p>Lorem ipsum dolor sit amet, consectetur adipiscing elit, sed do eiusmod tempor incididunt</p></div>
<div class="service" style="left:871px;top:1582px"><div class="icon soft"><span><svg width="40" height="40" viewBox="0 0 40 40"><circle cx="20" cy="20" r="10" stroke="#fff" stroke-width="2.5" fill="none"/><circle cx="20" cy="20" r="3" fill="#fff"/></svg></span></div><h3>Maintenance Management</h3><p>Lorem ipsum dolor sit amet, consectetur adipiscing elit, sed do eiusmod tempor incididunt</p></div>

<div class="service" style="left:116px;top:1882px"><div class="icon soft"><span><svg width="40" height="40" viewBox="0 0 40 40"><circle cx="20" cy="20" r="10" stroke="#fff" stroke-width="2.5" fill="none"/><circle cx="20" cy="20" r="3" fill="#fff"/></svg></span></div><h3>Maintenance Execution</h3><p>Lorem ipsum dolor sit amet, consectetur adipiscing elit, sed do eiusmod tempor incididunt</p></div>
<div class="service" style="left:367px;top:1882px"><div class="icon"><span><svg width="40" height="40" viewBox="0 0 40 40"><circle cx="20" cy="20" r="10" stroke="#fff" stroke-width="2.5" fill="none"/><circle cx="20" cy="20" r="3" fill="#fff"/></svg></span></div><h3>Manufacturing Performance</h3><p>Lorem ipsum dolor sit amet, consectetur adipiscing elit, sed do eiusmod tempor incididunt</p></div>
<div class="service" style="left:619px;top:1882px"><div class="icon soft"><span><svg width="40" height="40" viewBox="0 0 40 40"><circle cx="20" cy="20" r="10" stroke="#fff" stroke-width="2.5" fill="none"/><circle cx="20" cy="20" r="3" fill="#fff"/></svg></span></div><h3>SCADA</h3><p>Lorem ipsum dolor sit amet, consectetur adipiscing elit, sed do eiusmod tempor incididunt</p></div>
<div class="service" style="left:871px;top:1882px"><div class="icon"><span><svg width="40" height="40" viewBox="0 0 40 40"><circle cx="20" cy="20" r="10" stroke="#fff" stroke-width="2.5" fill="none"/><circle cx="20" cy="20" r="3" fill="#fff"/></svg></span></div><h3>Vision Inspection Systems</h3><p>Lorem ipsum dolor sit amet, consectetur adipiscing elit, sed do eiusmod tempor incididunt</p></div>

<div class="btn" style="left:501px;top:2209px;width:199px;height:50px;background:var(--mid)">View All Services <svg viewBox="0 0 16 16"><circle cx="8" cy="8" r="8" fill="#fff"/><path d="M6 4.5L9.5 8 6 11.5" stroke="#85acd3" stroke-width="2" fill="none"/></svg></div>

<!-- testimonials -->
<div class="abs reviews" role="img" aria-label="Engineer working on industrial machinery, softened in pale blue"></div>
<h2 class="abs heading section-title" style="top:2463px;color:#fff">WHAT OUR USERS SAY</h2>

<div class="card" style="left:112px"><div class="quote">“</div><p>Lorem ipsum dolor sit amet, consectetur adipiscing elit, sed do eiusmod tempor incididunt ut labore et dolor</p><div class="person"><div class="avatar" role="img" aria-label="Client portrait"></div><div><strong>Daniel Hartley</strong><span>Businessman</span></div></div></div>
<div class="card featured" style="left:442px"><div class="quote">“</div><p>Lorem ipsum dolor sit amet, consectetur adipiscing elit, sed do eiusmod tempor incididunt ut labore et dolor</p><div class="person"><div class="avatar" role="img" aria-label="Client portrait"></div><div><strong>Daniel Hartley</strong><span>Businessman</span></div></div></div>
<div class="card" style="left:771px"><div class="quote">“</div><p>Lorem ipsum dolor sit amet, consectetur adipiscing elit, sed do eiusmod tempor incididunt ut labore et dolor</p><div class="person"><div class="avatar" role="img" aria-label="Client portrait"></div><div><strong>Daniel Hartley</strong><span>Businessman</span></div></div></div>

<!-- footer -->
<footer class="abs footer"></footer>
<h4 class="abs foot-h" style="left:112px;top:2958px;color:#fff;font-size:16px">Contact Form</h4>
<div class="field" style="left:112px;top:3001px;width:222px;height:44px">Name</div>
<div class="field" style="left:345px;top:3001px;width:222px;height:44px">Phone</div>
<div class="field" style="left:112px;top:3052px;width:455px;height:44px">Email</div>
<div class="field" style="left:112px;top:3103px;width:456px;height:78px;padding-top:6px">Message</div>
<div class="btn" style="left:112px;top:3190px;width:117px;height:43px;border-radius:22px;background:var(--mid)">Submit</div>

<h4 class="abs foot-h" style="left:628px;top:2960px;color:#fff;font-size:14px">Contact Info</h4>
<div class="info-row" style="top:2988px;color:#fff"><span class="dot"><svg width="14" height="14" viewBox="0 0 24 24"><path d="M12 2a7 7 0 00-7 7c0 5 7 13 7 13s7-8 7-13a7 7 0 00-7-7zm0 9.5A2.5 2.5 0 1112 6.5a2.5 2.5 0 010 5z" fill="#85acd3"/></svg></span><span>48 Harbour Lane<br>NSW 2000</span></div>
<div class="info-row" style="top:3057px;color:#fff"><span class="dot"><svg width="14" height="14" viewBox="0 0 24 24"><path d="M6.6 10.8a15 15 0 006.6 6.6l2.2-2.2a1 1 0 011-.25 11.4 11.4 0 003.6.57 1 1 0 011 1V20a1 1 0 01-1 1A17 17 0 013 4a1 1 0 011-1h3.5a1 1 0 011 1c0 1.25.2 2.45.57 3.6a1 1 0 01-.25 1z" fill="#85acd3"/></svg></span><span>1 800 555 0142</span></div>
<div class="info-row" style="top:3108px;color:#fff"><span class="dot"><svg width="14" height="14" viewBox="0 0 24 24"><rect x="3" y="6" width="18" height="12" rx="1" stroke="#85acd3" stroke-width="2" fill="none"/><path d="M3 7l9 6 9-6" stroke="#85acd3" stroke-width="2" fill="none"/></svg></span><span>info@corlettassociates.com</span></div>
<h4 class="abs foot-h" style="left:628px;top:3172px;color:#fff;font-size:16px">Stay Connected</h4>
<span class="social" style="left:805px;top:3170px;background:#3b5998"></span>
<span class="social" style="left:843px;top:3170px;background:#1da1f2"></span>
<span class="social" style="left:881px;top:3170px;background:#dd4b39"></span>
<span class="social" style="left:919px;top:3170px;background:#0077b5"></span>
<span class="social" style="left:957px;top:3170px;background:#e52d27"></span>

<h4 class="abs foot-h" style="left:953px;top:2960px;color:#fff;font-size:14px">Quick Links</h4>
<ul class="abs links" style="color:#fff"><li>Home</li><li>About Us</li><li>Our Services</li><li>Latest Blog</li><li>Contact Us</li></ul>

<div class="abs foot-rule"></div>
<p class="abs" style="left:112px;top:3284px;font-size:14px;color:#fff">© 2021 Corlett Associates. All Rights reserved</p>
<div class="abs" style="left:944px;top:3281px;display:flex;align-items:center;gap:8px;color:#fff;font-size:15px;font-weight:700"><span style="width:22px;height:22px;background:var(--mid)"></span>VALTRIX ENGINEERING</div>

</body>
</html>
```